New business card/stationary for a consulting company

I am looking for a clean and very professional looking business card for my consulting company as well as corresponding stationary. I am uploading our logo. I like simple and powerful for the feel. No graphics but I am open on everything else. Below is my contact information but would like the final to be in a version I can add my employees information into and print. Thank you.

Daniel Whitcombe
dan@ferncliffadvisory.com
2870 North 9th Avenue, Summit Floor, Elm Ridge, Illinois 60531
www.ferncliffadvisory.com

Industry/Entity Type

Consulting

Contact Information for Business Card

Daniel Whitcombe
dan@ferncliffadvisory.com
www.ferncliffadvisory.com

Font styles to use
Serif
Sans Serif

Requirements
Must have
• Our logo and the business card details.
Nice to have
• our website www.ferncliffadvisory.com

```html
<!DOCTYPE html>
<html lang="en">
<head>
<meta charset="utf-8">
<title>Ferncliff Advisory – Business Card</title>
<link rel="stylesheet" href="https://fonts.googleapis.com/css2?family=Montserrat:wght@400;500;700&display=swap">
<style>
  :root {
    --navy: #14116e;
    --navy-deep: #0f0d5c;
    --white: #ffffff;
    --ink: #2a2a3a;
    --backdrop: #e4e4e6;
  }
  * { box-sizing: border-box; margin: 0; padding: 0; }
  html, body {
    width: 1200px; height: 1022px; overflow: hidden;
    background: var(--backdrop);
    font-family: "Montserrat", Arial, sans-serif;
  }
  .card {
    position: absolute; left: 200px;
    width: 800px; height: 457px;
    box-shadow: 0 6px 18px rgba(0,0,0,.18);
  }
  .card-front { top: 36px; background: linear-gradient(135deg, var(--navy) 0%, var(--navy-deep) 100%); color: var(--white); }
  .card-back { top: 529px; background: var(--white); color: var(--navy); }

  /* front */
  .front-brand {
    position: absolute; top: 150px; left: 0; width: 100%;
    display: flex; align-items: center; justify-content: center; gap: 18px;
  }
  .brand-square { width: 46px; height: 46px; background: var(--white); }
  .front-brand .brand-name { font-size: 40px; font-weight: 400; letter-spacing: 1px; color: var(--white); }
  .front-rule {
    position: absolute; top: 300px; left: 70px; right: 70px;
    display: flex; align-items: center; gap: 18px;
  }
  .front-rule .line { flex: 1; height: 2px; background: var(--white); }
  .front-rule .site { font-size: 15px; font-weight: 700; letter-spacing: .3px; }
  .front-base { position: absolute; top: 360px; left: 70px; right: 70px; height: 2px; background: rgba(255,255,255,.85); }

  /* back */
  .back-brand { position: absolute; top: 120px; left: 70px; display: flex; align-items: center; gap: 14px; }
  .back-brand .brand-square { width: 36px; height: 36px; background: var(--navy); }
  .back-brand .brand-name { font-size: 30px; font-weight: 400; letter-spacing: .5px; color: var(--navy); }
  .brand-rule { position: absolute; top: 190px; left: 70px; width: 480px; height: 2px; background: var(--navy); }

  .person { position: absolute; top: 112px; right: 70px; text-align: right; }
  .person-name { font-size: 22px; font-weight: 700; color: var(--navy); }
  .person-rule { height: 2px; background: var(--navy); width: 190px; margin: 6px 0 5px auto; }
  .person-title { font-size: 13px; font-weight: 700; color: var(--navy); }

  .address { position: absolute; top: 210px; right: 70px; text-align: right; font-size: 14px; line-height: 1.7; color: var(--ink); }

  .contact-rule { position: absolute; top: 282px; left: 70px; width: 320px; height: 2px; background: var(--navy); }
  .contacts { position: absolute; top: 298px; left: 70px; list-style: none; }
  .contacts li { display: flex; align-items: center; gap: 14px; font-size: 15px; color: var(--ink); height: 28px; }
  .contacts svg { width: 15px; height: 15px; fill: var(--navy); flex: none; }
</style>
</head>
<body>

<section class="card card-front" aria-label="Card front">
  <div class="front-brand">
    <span class="brand-square"></span>
    <span class="brand-name">FERNCLIFF ADVISORY</span>
  </div>
  <div class="front-rule">
    <span class="line"></span>
    <span class="site">www.ferncliffadvisory.com</span>
    <span class="line"></span>
  </div>
  <div class="front-base"></div>
</section>

<section class="card card-back" aria-label="Card back">
  <div class="back-brand">
    <span class="brand-square"></span>
    <span class="brand-name">FERNCLIFF ADVISORY</span>
  </div>
  <div class="brand-rule"></div>

  <div class="person">
    <div class="person-name">Daniel Whitcombe</div>
    <div class="person-rule"></div>
    <div class="person-title">Founder / Principal</div>
  </div>

  <address class="address" style="font-style:normal">
    2870 North 9th Avenue, Summit Floor,<br>
    Elm Ridge, Illinois 60531
  </address>

  <div class="contact-rule"></div>
  <ul class="contacts">
    <li>
      <svg viewBox="0 0 24 24" aria-hidden="true"><path d="M6.6 10.8a15 15 0 0 0 6.6 6.6l2.2-2.2c.3-.3.7-.4 1-.2 1.1.4 2.3.6 3.6.6.6 0 1 .4 1 1V20c0 .6-.4 1-1 1A17 17 0 0 1 3 4c0-.6.4-1 1-1h3.5c.6 0 1 .4 1 1 0 1.3.2 2.5.6 3.6.1.3 0 .7-.2 1z"/></svg>
      (855) 555 01472
    </li>
    <li>
      <svg viewBox="0 0 24 24" aria-hidden="true"><path d="M7 1h10a2 2 0 0 1 2 2v18a2 2 0 0 1-2 2H7a2 2 0 0 1-2-2V3a2 2 0 0 1 2-2zm0 3v14h10V4zm5 15.5a1 1 0 1 0 0 2 1 1 0 0 0 0-2z"/></svg>
      + 1 312 555 0198
    </li>
    <li>
      <svg viewBox="0 0 24 24" aria-hidden="true"><path d="M2 5h20v14H2zm2 2v.5l8 5 8-5V7z"/></svg>
      dan@ferncliffadvisory.com
    </li>
    <li>
      <svg viewBox="0 0 24 24" aria-hidden="true"><path d="M12 2a10 10 0 1 0 0 20 10 10 0 0 0 0-20zm6.9 6h-3a15 15 0 0 0-1.3-3.9A8 8 0 0 1 18.9 8zM12 4c.8 1.2 1.5 2.5 1.9 4h-3.8c.4-1.5 1.1-2.8 1.9-4zM4.3 14a8 8 0 0 1 0-4h3.4a16 16 0 0 0 0 4zm.8 2h3a15 15 0 0 0 1.3 3.9A8 8 0 0 1 5.1 16zm3-8h-3a8 8 0 0 1 4.3-3.9C8.8 5.3 8.4 6.6 8.1 8zM12 20c-.8-1.2-1.5-2.5-1.9-4h3.8c-.4 1.5-1.1 2.8-1.9 4zm2.3-6H9.7a14 14 0 0 1 0-4h4.6a14 14 0 0 1 0 4zm.3 5.9c.6-1.2 1-2.5 1.3-3.9h3a8 8 0 0 1-4.3 3.9zM16.3 14a16 16 0 0 0 0-4h3.4a8 8 0 0 1 0 4z"/></svg>
      www.ferncliffadvisory.com
    </li>
  </ul>
</section>

</body>
</html>
```